Design of Labels for Harbour Reef Gin bottle

Design bottle labels for Harbour Reef Gin. There are three labels to design; a front, a back and a tamper band to be placed over the cork. The labels should be deigned to fit the bottle specified in the link below.
The Gin is an excellent high end premium brand Navy strength Gin 57% Vol. The bottle should evoke excellence and a romance of period of pride in the British Navy. Gin was drunk by officers in the Navy so a representation of the Officer Class should be made possibly through gold braid of a senior officer's sleeve, cap or lapel. The white ensign should also be prominent. Suggested colour themes are navy blues, grey, and white....although others schemes may be suitable. Corley's Dock Rum is a good example of the sort of thing we are looking for, although the design must not be so similar that it encroaches on Corley's trade mark or copyrights. The period theme is 1900 to 1940
Bottle link: https://www.vessel-crate-depot.co.uk/Glass-bottles/350ml-flint-glass-bottle-Marta.html
Target Market(s)
Gin Drinkers
Look and feel
Each slider illustrates characteristics of the customer's brand and the style your logo design should communicate.

```html
<!DOCTYPE html>
<html lang="en">
<head>
<meta charset="utf-8">
<title>Harbour Reef Gin – Front Label</title>
<link rel="stylesheet" href="https://fonts.googleapis.com/css2?family=Playfair+Display:wght@700;900&family=Pinyon+Script&family=Oswald:wght@400;500&display=swap">
<style>
  :root {
    --backdrop: #1d1e2c;
    --navy: #1c2233;
    --paper: #ffffff;
    --gold: #c9a24a;
    --gold-dark: #9c7a2c;
    --tag-grey: #6b6b70;
  }
  * { box-sizing: border-box; margin: 0; padding: 0; }
  html, body {
    width: 1200px; height: 1200px; overflow: hidden;
    background: var(--backdrop);
  }
  .canvas {
    position: relative; width: 1200px; height: 1200px;
  }
  .label {
    position: absolute; left: 270px; top: 120px;
    width: 660px; height: 960px;
    border-radius: 26px; overflow: hidden;
    background: var(--paper);
  }
  .label__top {
    position: absolute; left: 0; top: 0; width: 100%; height: 470px;
    background: var(--paper);
  }
  .label__bottom {
    position: absolute; left: 0; top: 470px; width: 100%; height: 490px;
    background: var(--navy);
  }
  .frame {
    position: absolute; left: 20px; right: 20px;
    border: 8px double var(--navy);
  }
  .frame--top { top: 20px; bottom: 0; border-bottom: none; border-radius: 12px 12px 0 0; }
  .frame--bottom { top: 0; bottom: 20px; border-top: none; border-color: var(--paper); border-radius: 0 0 12px 12px; }

  .brand-arch { position: absolute; left: 0; top: 30px; width: 660px; height: 200px; }
  .brand-arch text {
    font-family: 'Playfair Display', serif; font-weight: 900;
    font-size: 78px; letter-spacing: 4px; fill: var(--navy);
  }
  .crest {
    position: absolute; left: 150px; top: 165px; width: 360px; height: 280px;
    border-radius: 50% 50% 44% 44%;
    background: radial-gradient(circle at 50% 48%, var(--navy) 0 26%, var(--paper) 27% 31%, var(--gold) 32% 48%, rgba(201,162,74,0.25) 62%, rgba(255,255,255,0) 72%);
  }
  .est-tag {
    position: absolute; top: 306px; width: 64px; height: 24px;
    background: var(--tag-grey); color: var(--paper);
    font-family: 'Oswald', sans-serif; font-size: 14px; letter-spacing: 1px;
    display: flex; align-items: center; justify-content: center;
  }
  .est-tag--left { left: 58px; }
  .est-tag--right { right: 58px; }

  .braid { position: absolute; left: 120px; top: 60px; width: 420px; }
  .braid__stripe {
    height: 18px; margin-bottom: 12px;
    background: var(--paper); border-radius: 3px;
  }
  .product-name {
    position: absolute; left: 0; width: 100%; top: 208px;
    text-align: center; color: var(--paper);
    font-family: 'Playfair Display', serif; font-weight: 700;
    font-size: 80px; letter-spacing: 2px; line-height: 1;
  }
  .tagline {
    position: absolute; left: 0; width: 100%; top: 310px;
    text-align: center; color: var(--gold);
    font-family: 'Pinyon Script', cursive; font-size: 46px; line-height: 1;
  }
  .rule {
    position: absolute; left: 120px; right: 120px; top: 372px;
    height: 2px; background: var(--gold-dark);
  }
  .spec-line {
    position: absolute; left: 120px; right: 120px; top: 398px;
    display: flex; justify-content: space-between;
    font-family: 'Oswald', sans-serif; font-weight: 500; font-size: 22px;
    color: var(--gold); letter-spacing: 0.5px;
  }
</style>
</head>
<body>
<main class="canvas">
  <section class="label" aria-label="Harbour Reef Gin front label">
    <div class="label__top">
      <div class="frame frame--top"></div>
      <svg class="brand-arch" viewBox="0 0 660 200" aria-label="Harbour">
        <defs>
          <path id="brand-arc" d="M120 190 A 230 170 0 0 1 540 190"/>
        </defs>
        <text><textPath href="#brand-arc" startOffset="50%" text-anchor="middle">HARBOUR</textPath></text>
      </svg>
      <div class="crest" role="img" aria-label="Crest with crown, crossed anchors, two gold lions and a roped anchor roundel"></div>
      <div class="est-tag est-tag--left">EST.</div>
      <div class="est-tag est-tag--right">2018</div>
    </div>
    <div class="label__bottom">
      <div class="frame frame--bottom"></div>
      <div class="braid" aria-hidden="true">
        <div class="braid__stripe"></div>
        <div class="braid__stripe"></div>
        <div class="braid__stripe"></div>
        <div class="braid__stripe"></div>
      </div>
      <h1 class="product-name">REEF GIN</h1>
      <p class="tagline">Premium Blend</p>
      <div class="rule"></div>
      <p class="spec-line"><span>57 % vol</span><span>PRODUCT OF ENGLAND</span><span>350 ml</span></p>
    </div>
  </section>
</main>
</body>
</html>
```